Website Design for Employee Moral and Happiness Company

Looking for a clean website design that explains our features in a step by step manner so our visitors know exactly what our site does before logging in.

The site is called "Velrato". See logo design and video for a sample of style and an overview of what we do.

Target Market(s)

Business owners that are looking to retain employees.

Number of Pages Required

1 page

```html
<!DOCTYPE html>
<html lang="en">
<head>
<meta charset="UTF-8">
<title>Velrato — What is velrato?</title>
<link rel="stylesheet" href="https://fonts.googleapis.com/css2?family=Spectral:wght@700;800&family=Nunito:wght@400;600;800&family=Josefin+Sans:wght@600&display=swap">
<style>
  :root {
    --bg: #e8dfd6;
    --ink: #2f2d2c;
    --muted: #3d3a38;
    --accent: #ff6a00;
    --rule: #f3ede7;
    --dot: #4a4f63;
    --stepper: #6e6a67;
    --white: #ffffff;
    --video-top: #45403b;
    --video-mid: #3a3531;
    --video-bottom: #2e2a27;
  }
  * { box-sizing: border-box; margin: 0; padding: 0; }
  html, body {
    width: 1200px; height: 698px; overflow: hidden;
    background: var(--bg);
    font-family: "Nunito", sans-serif;
    color: var(--ink);
  }
  .page { position: relative; width: 1200px; height: 698px; }

  .site-header {
    position: absolute; left: 0; top: 0; width: 1200px; height: 89px;
    border-bottom: 2px solid var(--rule);
  }
  .brand {
    position: absolute; left: 66px; top: 18px;
    font-family: "Spectral", serif; font-weight: 800; font-size: 42px;
    color: #111; letter-spacing: 0.5px; line-height: 1;
    display: flex; align-items: center; gap: 8px;
  }
  .brand-dot { width: 12px; height: 12px; border-radius: 50%; background: var(--accent); margin-top: 10px; }

  .main-nav a {
    position: absolute; top: 34px; font-size: 15.5px; color: var(--muted);
    text-decoration: none; white-space: nowrap;
  }
  .main-nav a.is-active { color: var(--accent); border-bottom: 1px solid var(--accent); }

  .login {
    position: absolute; left: 906px; top: 34px; font-size: 15.5px; color: var(--muted);
    display: flex; align-items: center; gap: 9px;
  }
  .signup {
    position: absolute; left: 995px; top: 18px; width: 141px; height: 45px;
    border-radius: 23px; background: var(--accent); color: var(--white);
    font-weight: 800; font-size: 16px; display: flex; align-items: center; justify-content: center;
  }

  .section-title {
    position: absolute; left: 0; width: 1200px; top: 112px; text-align: center;
    font-family: "Spectral", serif; font-weight: 700; font-size: 32px; color: var(--ink);
  }

  .dot-grid { position: absolute; }
  .dot-grid--top { left: 910px; top: 152px; }
  .dot-grid--bottom { left: 192px; top: 572px; }

  .video {
    position: absolute; left: 224px; top: 199px; width: 749px; height: 422px;
    background: linear-gradient(180deg, var(--video-top) 0%, var(--video-mid) 60%, var(--video-bottom) 100%);
  }
  .video-play {
    position: absolute; left: 340px; top: 150px;
  }
  .video-caption {
    position: absolute; left: 0; width: 100%; top: 255px; text-align: center;
    font-family: "Josefin Sans", sans-serif; font-weight: 600; font-size: 17px;
    letter-spacing: 1.2px; color: var(--white);
  }

  .stepper { position: absolute; left: 0; top: 0; }
  .stepper-label {
    position: absolute; right: 40px; top: 468px;
    font-size: 11.5px; font-weight: 800; color: var(--ink); white-space: nowrap;
  }
</style>
</head>
<body>
<div class="page">
  <header class="site-header">
    <div class="brand">velrato<span class="brand-dot"></span></div>
    <nav class="main-nav">
      <a class="is-active" style="left:278px">Home</a>
      <a style="left:342px">Boring Work Events</a>
      <a style="left:499px">Introducing Velrato</a>
      <a style="left:654px">Why Velrato</a>
      <a style="left:767px">Testimonials</a>
    </nav>
    <div class="login">
      <svg width="12" height="12" viewBox="0 0 12 12" fill="none" stroke="#3d3a38" stroke-width="1.2">
        <path d="M1 6h6M5 3.5 7.5 6 5 8.5M10 1.5v9"/>
      </svg>
      Login
    </div>
    <div class="signup">SIGN UP</div>
  </header>

  <h1 class="section-title">What is velrato ?</h1>

  <svg class="dot-grid dot-grid--top" width="120" height="100" aria-hidden="true">
    <defs><pattern id="dotsA" width="18.75" height="21.5" patternUnits="userSpaceOnUse"><circle cx="4" cy="4" r="2.1" fill="#4a4f63"/></pattern></defs>
    <rect width="131" height="100" fill="url(#dotsA)"/>
  </svg>
  <svg class="dot-grid dot-grid--bottom" width="131" height="100" aria-hidden="true">
    <defs><pattern id="dotsB" width="18.75" height="21.5" patternUnits="userSpaceOnUse"><circle cx="4" cy="4" r="2.1" fill="#4a4f63"/></pattern></defs>
    <rect width="131" height="100" fill="url(#dotsB)"/>
  </svg>

  <div class="video" role="img" aria-label="Illustrated video still of colleagues chatting in a lounge with armchairs">
    <svg class="video-play" width="70" height="70" viewBox="0 0 70 70" fill="none" stroke="#fff" stroke-width="2.6">
      <circle cx="35" cy="35" r="33.5"/>
      <path d="M28 22v26l20-13z" stroke-linejoin="round"/>
    </svg>
    <div class="video-caption">WHAT IS VELRATO?</div>
  </div>

  <svg class="stepper" width="1200" height="698" aria-hidden="true">
    <line x1="1175" y1="270" x2="1175" y2="517" stroke="#6e6a67" stroke-width="1.5"/>
    <g fill="#e8dfd6" stroke="#6e6a67" stroke-width="1.6">
      <circle cx="1175" cy="270" r="5.6"/>
      <circle cx="1175" cy="311" r="5.6"/>
      <circle cx="1175" cy="352.5" r="5.6"/>
      <circle cx="1175" cy="394" r="5.6"/>
      <circle cx="1175" cy="435" r="5.6"/>
      <circle cx="1175" cy="517.5" r="5.6"/>
    </g>
    <circle cx="1175" cy="476" r="11" fill="#b3aca6"/>
    <circle cx="1175" cy="476" r="6" fill="#3a3735"/>
  </svg>
  <div class="stepper-label">What is velrato?</div>
</div>
</body>
</html>
```